redesign my website bluekeelvoyages.net and make it user friendly

I already have a website, bluekeelvoyages.net, and want a redesign in WordPress with Elementor Pro, using the same text/content. The goal is to improve:

Design quality (colors, fonts, spacing, visual flow)
User experience (easy navigation, clear offers)
Conversion readiness (calls-to-action, trust signals, booking flow)
Technical side (SEO basics, fast speed, full mobile responsiveness)

The site should look modern, clean, fun, engaging, interactive and optimized for speed and usability.

I would like the 11 page to be consolidate dto 6 as follows: Home (main landing, highlights)

Sailboat Trips (all packages, itineraries, pricing)
Boats (fleet details, features, photos)
How It Works (booking process, FAQs, travel info, what to expect)
Blog
Contact Us (form, WhatsApp, phone, etc.)

Target Market(s)

sailboat trip customers for San Blas Islands in Panama

Industry/Entity Type

Travel, Boat Tour Agency

Coding

Coded - Design and coding required

Number of Pages Required

3 page

Font styles to use
Sans Serif
Other font styles liked:
• Oswalg and sans serif

Colors
0054AA
0677BA
7BADD7
CADEEF
E8F1F8
0094D4
00A9DD
6FCCEA
C7EBF8
E9F6FB
FFC000
F8CF3A
FAE287
FDF2CF
FEFAEE
F0912C
F2A743
F7CA91
FBE8D2
FDF5EE

Requirements
Must have
• Home (main landing, highlights) Sailboat Trips (all packages, itineraries, pricing) Boats (fleet details, features, photos) How It Works (booking process, FAQs, travel info, what to expect) Blog (updates, travel tips, inspiration) Contact Us (form, WhatsApp, phone, etc.)
Nice to have
• I want it to look professionla and be very user friendy to entice people to contact me to book boat trips
Should not have
• a store

```html
<!DOCTYPE html>
<html lang="en">
<head>
<meta charset="utf-8">
<title>Blue Keel Voyages – San Blas Sailing</title>
<link href="https://fonts.googleapis.com/css2?family=Oswald:wght@500;600&family=Poppins:wght@300;400;500;600&display=swap" rel="stylesheet">
<style>
:root{
  --orange:#F0912C;
  --orange-soft:#F7CA91;
  --ink:#124E66;
  --ink-dark:#0B3A4F;
  --text:#333;
  --muted:#666;
  --grey-card:#F2F2F2;
  --blue-card:#E9F6FB;
  --line:#E3E3E3;
  --white:#fff;
}
*{box-sizing:border-box;margin:0;padding:0}
html,body{width:1200px;height:4751px;overflow:hidden}
body{position:relative;font-family:'Poppins',sans-serif;color:var(--text);background:var(--white)}
.abs{position:absolute}

/* header */
.site-header{left:0;top:0;width:1200px;height:138px;background:#F4FAFD}
.brand{left:66px;top:66px;font-family:'Oswald',sans-serif;font-weight:600;font-size:30px;color:var(--ink);letter-spacing:.2px}
.btn-pill{height:39px;border-radius:20px;color:#fff;font-size:14px;font-weight:500;display:flex;align-items:center;justify-content:center;text-transform:uppercase}
.btn-book{left:833px;top:29px;width:144px;background:var(--orange)}
.btn-contact{left:992px;top:29px;width:142px;background:var(--ink)}
.main-nav{top:86px;font-size:14px;font-weight:500;color:#222;text-transform:uppercase}
.main-nav .caret{color:var(--orange);font-size:9px;margin-left:3px}
.nav-active{color:var(--ink)}

/* hero */
.hero{left:0;top:138px;width:1200px;height:824px;overflow:hidden}
.hero-media{position:absolute;inset:0;background:linear-gradient(180deg,#2a7cb4 0%,#2379b0 25%,#1a6aa0 45%,#0f5a8e 65%,#0b4b7a 100%)}
.hero-title{left:105px;top:188px;font-family:'Oswald',sans-serif;font-weight:600;font-size:104px;color:#fff;line-height:1}
.hero-sub{left:116px;top:322px;font-size:21px;color:#fff}
.hero-cta{left:110px;top:396px;width:297px;height:60px;border-radius:30px;background:var(--orange);color:#fff;font-weight:600;font-size:19px;display:flex;align-items:center;justify-content:center;gap:10px}
.hero-arrow{width:44px;height:44px;border-radius:50%;display:flex;align-items:center;justify-content:center}
.hero-prev{left:8px;top:343px;background:rgba(255,255,255,.25)}
.hero-next{left:1134px;top:343px;background:#fff}
.hero-dots{left:575px;top:734px;display:flex;gap:6px}
.hero-dots span{width:9px;height:9px;border-radius:50%;border:1.5px solid #fff}
.hero-dots span.on{background:#fff}

/* boats & prices */
.section-title{left:0;width:1200px;text-align:center;top:1062px;font-weight:300;font-size:50px;color:var(--ink);letter-spacing:.5px}
.divider{left:500px;top:1149px;width:200px;height:8px}
.group-title{left:0;width:1200px;text-align:center;font-weight:600;font-size:31px;color:var(--ink)}
.price-row{left:0;width:1200px;height:200px}
.card{position:absolute;width:300px;border-radius:6px;text-align:center;border:1px solid var(--line);padding-top:22px}
.card.grey{background:var(--grey-card)}
.card.blue{background:var(--blue-card)}
.card.faded{opacity:.4}
.card h3{font-size:20px;font-weight:600;color:var(--orange);margin-bottom:12px}
.card p{font-size:16px;line-height:27px;color:#222}
.card .more{display:inline-block;margin-top:22px;width:130px;height:28px;line-height:28px;border-radius:14px;background:var(--orange);color:#fff;font-size:13px;font-weight:500}
.row-next{position:absolute;left:1106px;width:44px;height:44px;border-radius:50%;background:var(--ink);display:flex;align-items:center;justify-content:center}

/* descriptions */
.desc-title{left:0;width:1200px;text-align:center;top:3190px;font-weight:600;font-size:48px;color:var(--ink)}
.desc-card{position:absolute;top:3323px;width:348px;background:#F3F3F3;border:1px solid var(--line);border-radius:6px;padding:14px 14px 20px;text-align:center}
.desc-media{width:320px;height:254px;border-radius:4px}
.desc-card h3{font-size:20px;font-weight:600;color:var(--ink);margin:22px 0 14px}
.desc-card p{font-size:13px;line-height:23.5px;color:#333;padding:0 6px}
.desc-arrow{width:44px;height:44px;border-radius:50%;display:flex;align-items:center;justify-content:center}
.desc-prev{left:-4px;top:3533px;border:1px solid #ccc;background:#fff}
.desc-next{left:1150px;top:3533px;background:var(--orange)}

/* footer */
.site-footer{left:0;top:4313px;width:1200px;height:438px;background:var(--ink-dark);color:#fff}
.foot-head{font-size:18px;font-weight:500;color:#6FCCEA;top:94px}
.foot-head::after{content:"";display:block;width:58px;height:1px;background:#6FCCEA;margin-top:14px}
.links{display:grid;grid-template-columns:130px 130px;row-gap:14px;top:182px;left:124px;font-size:13px}
.links a{color:#fff;text-decoration:none}
.links a::before{content:"»";color:#6FCCEA;margin-right:12px}
.contact-list{top:178px;left:461px;font-size:12.5px;line-height:17px}
.contact-item{display:flex;gap:18px;margin-bottom:16px;align-items:flex-start}
.contact-icon{width:26px;height:26px;border:1px solid #9bbac8;border-radius:3px;display:flex;align-items:center;justify-content:center;flex-shrink:0}
.news-input{left:794px;top:186px;width:332px;height:46px;background:#15607d;font-size:10px;font-weight:600;padding-left:20px;display:flex;align-items:center;text-transform:uppercase}
.news-btn{left:794px;top:256px;width:168px;height:34px;background:var(--orange);font-size:11px;font-weight:600;display:flex;align-items:center;justify-content:center;text-transform:uppercase}
.foot-rule{left:61px;top:363px;width:1076px;height:1px;background:#5c7d8c}
.copyright{left:61px;top:394px;font-size:11px}
.social{left:974px;top:381px;display:flex;gap:10px}
.social span{width:32px;height:32px;border:1px solid #fff;border-radius:3px;display:flex;align-items:center;justify-content:center}
.social span i{width:10px;height:10px;background:#fff;display:block}
</style>
</head>
<body>

<header class="site-header abs">
  <div class="brand abs">Blue Keel Voyages</div>
  <a class="btn-pill btn-book abs">Book Now</a>
  <a class="btn-pill btn-contact abs">Contact Us</a>
  <nav>
    <span class="main-nav abs" style="left:470px">Sailboat Trips<span class="caret">▼</span></span>
    <span class="main-nav nav-active abs" style="left:675px">Boats &amp; Prices<span class="caret">▼</span></span>
    <span class="main-nav abs" style="left:881px">How It Works<span class="caret">▼</span></span>
    <span class="main-nav abs" style="left:1082px">Blog</span>
  </nav>
</header>

<section class="hero abs">
  <div class="hero-media" role="img" aria-label="Catamaran sailing on deep blue open sea with a motor yacht behind"></div>
  <h1 class="hero-title abs">San Blas Islands</h1>
  <p class="hero-sub abs">Panama Sailing Vacations.Ultimate Beaches &amp; Catamaran Tours</p>
  <a class="hero-cta abs">CHARTER INQUIRY FORM
    <svg width="22" height="20" viewBox="0 0 22 20" fill="none" stroke="#fff" stroke-width="2"><path d="M13 3H5a2 2 0 0 0-2 2v10a2 2 0 0 0 2 2h8"/><path d="M9 10h11M16 6l4 4-4 4"/></svg>
  </a>
  <span class="hero-arrow hero-prev abs"><svg width="12" height="12" viewBox="0 0 12 12"><path d="M8 2 4 6l4 4" stroke="#fff" stroke-width="2" fill="none"/></svg></span>
  <span class="hero-arrow hero-next abs"><svg width="12" height="12" viewBox="0 0 12 12"><path d="m4 2 4 4-4 4" stroke="#222" stroke-width="2" fill="none"/></svg></span>
  <div class="hero-dots abs"><span class="on"></span><span></span><span></span><span></span></div>
</section>

<h2 class="section-title abs">BOATS AND PRICES</h2>
<svg class="divider abs" viewBox="0 0 200 8"><line x1="0" y1="4" x2="200" y2="4" stroke="#F7CA91" stroke-width="1"/><path d="M100 0 104 4 100 8 96 4Z" fill="#F0912C"/></svg>

<!-- Shared charter -->
<h2 class="group-title abs" style="top:1208px">SHARED CHARTER BOATS</h2>
<div class="price-row abs" style="top:1286px">
  <div class="card grey" style="left:-24px;height:155px"><h3>Sea Wander 45</h3><p>$750 per person for 3 nights<br>Capacity 8 / Sailboat</p><span class="more">MORE INFO</span></div>
  <div class="card grey" style="left:300px;height:155px"><h3>Coralia 42</h3><p>$870 per person for 3 nights<br>Capacity 8 / Catamaran</p><span class="more">MORE INFO</span></div>
  <div class="card grey" style="left:624px;height:155px"><h3>Tidewell 37</h3><p>$825 per person for 3 nights<br>Capacity 6 / Catamaran</p><span class="more">MORE INFO</span></div>
  <div class="card grey faded" style="left:948px;height:155px"><h3>Keelstar 395H</h3><p>$815 per person for 3 nights<br>Capacity 8 / Catamaran</p><span class="more" style="background:var(--orange-soft)">MORE INFO</span></div>
  <span class="row-next" style="top:50px"><svg width="12" height="12" viewBox="0 0 12 12"><path d="m4 2 4 4-4 4" stroke="#fff" stroke-width="2" fill="none"/></svg></span>
</div>

<!-- Luxury -->
<h2 class="group-title abs" style="top:1525px">LUXURY CATAMARANS</h2>
<div class="price-row abs" style="top:1603px">
  <div class="card blue" style="left:-24px;height:194px"><h3>Tidewell 55</h3><p>$1,400 for 2 guests<br>$200 per person for<br>additional guests<br>Capacity 8 / Catamaran</p></div>
  <div class="card blue" style="left:300px;height:194px"><h3>Coralia 42</h3><p>$900 for 2 guests<br>$125 per person for<br>additional guests<br>Capacity 8 / Catamaran</p></div>
  <div class="card blue" style="left:624px;height:194px"><h3>Tidewell 57N</h3><p>$1,400 for 2 guests<br>$200 per person for<br>additional guests<br>Capacity 8 / Catamaran</p></div>
  <div class="card blue faded" style="left:948px;height:194px"><h3>Tidewell 56</h3><p>$1,900 for 2 guests<br>$300 per person for<br>additional guests<br>Capacity 8 / Catamaran</p></div>
  <span class="row-next" style="top:52px"><svg width="12" height="12" viewBox="0 0 12 12"><path d="m4 2 4 4-4 4" stroke="#fff" stroke-width="2" fill="none"/></svg></span>
</div>

<!-- Budget -->
<h2 class="group-title abs" style="top:1848px">BUDGET FRIENDLY CATAMARANS</h2>
<div class="price-row abs" style="top:1926px">
  <div class="card grey" style="left:-24px;height:194px"><h3>Tidewell 37</h3><p>$900 for 2 guests<br>$125 per person for<br>additional guests<br>Capacity 6 / Catamaran</p></div>
  <div class="card grey" style="left:300px;height:194px"><h3>Coralia 42</h3><p>$900 for 2 guests<br>$125 per person for<br>additional guests<br>Capacity 8 / Catamaran</p></div>
  <div class="card grey" style="left:624px;height:194px"><h3>Keelstar 395H</h3><p>$1,000 for 2 guests<br>$150 per person for<br>additional guests<br>Capacity 8 / Catamaran</p></div>
  <div class="card grey faded" style="left:948px;height:194px"><h3>Keelstar 395K</h3><p>$1,000 for 2 guests<br>$150 per person for<br>additional guests<br>Capacity 6 / Catamaran</p></div>
  <span class="row-next" style="top:52px"><svg width="12" height="12" viewBox="0 0 12 12"><path d="m4 2 4 4-4 4" stroke="#fff" stroke-width="2" fill="none"/></svg></span>
</div>

<!-- Large -->
<h2 class="group-title abs" style="top:2172px">LARGE CATAMARANS (8 TO 12 GUESTS)</h2>
<div class="price-row abs" style="top:2250px">
  <div class="card blue" style="left:-24px;height:194px"><h3>Tidewell 47</h3><p>$1,200 for 2 guests<br>$180 per person for<br>additional guests<br>Capacity 8 / Catamaran</p></div>
  <div class="card blue" style="left:300px;height:194px"><h3>Tidewell 57N</h3><p>$1,400 for 2 guests<br>$200 per person for<br>additional guests<br>Capacity 8 / Catamaran</p></div>
  <div class="card blue" style="left:624px;height:194px"><h3>Tidewell 55</h3><p>$1,400 for 2 guests<br>$200 per person for<br>additional guests<br>Capacity 8 / Catamaran</p></div>
  <div class="card blue faded" style="left:948px;height:194px"><h3>Tidewell 55S</h3><p>$1,250 for 2 guests<br>$250 per person for<br>additional guests<br>Capacity 9 / Catamaran</p></div>
  <span class="row-next" style="top:52px"><svg width="12" height="12" viewBox="0 0 12 12"><path d="m4 2 4 4-4 4" stroke="#fff" stroke-width="2" fill="none"/></svg></span>
</div>

<!-- Mid-size -->
<h2 class="group-title abs" style="top:2497px">MID-SIZE CATAMARANS (6 TO 8 GUESTS)</h2>
<div class="price-row abs" style="top:2575px">
  <div class="card grey" style="left:-24px;height:194px"><h3>Tidewell 40S2</h3><p>$1,000 for 2 guests<br>$200 per person for<br>additional guests<br>Capacity 8 / Catamaran</p></div>
  <div class="card grey" style="left:300px;height:194px"><h3>Coralia 42</h3><p>$900 for 2 guests<br>$125 per person for<br>additional guests<br>Capacity 8 / Catamaran</p></div>
  <div class="card grey" style="left:624px;height:194px"><h3>Tidewell 44</h3><p>$1,200 for 2 guests<br>$200 per person for<br>additional guests<br>Capacity 8 / Catamaran</p></div>
  <div class="card grey faded" style="left:948px;height:194px"><h3>Keelstar 395K</h3><p>$1,000 for 2 guests<br>$150 per person for<br>additional guests<br>Capacity 6 / Catamaran</p></div>
  <span class="row-next" style="top:52px"><svg width="12" height="12" viewBox="0 0 12 12"><path d="m4 2 4 4-4 4" stroke="#fff" stroke-width="2" fill="none"/></svg></span>
</div>

<!-- Monohull -->
<h2 class="group-title abs" style="top:2821px">MONOHULL SAILBOATS</h2>
<div class="price-row abs" style="top:2899px">
  <div class="card blue" style="left:-24px;height:194px"><h3>Marevale</h3><p>$650 for 2 guests<br>$100 per person for additional<br>guests<br>Capacity 4 / Sailboat</p></div>
  <div class="card blue" style="left:300px;height:194px"><h3>Sea Wander</h3><p>$885 for 2 guests<br>$125 per person for<br>additional guests<br>Capacity 8 / Sailboat</p></div>
  <div class="card blue" style="left:624px;height:194px"><h3>Albatra 47</h3><p>$720 for 2 guests<br>$120 per person for<br>additional guests<br>Capacity 4 / Sailboat</p></div>
  <div class="card blue faded" style="left:948px;height:194px"><h3>Halden 73</h3><p>$750 for 2 guests<br>$200 per person for<br>additional guests<br>Capacity 6 / Sailboat</p></div>
  <span class="row-next" style="top:52px"><svg width="12" height="12" viewBox="0 0 12 12"><path d="m4 2 4 4-4 4" stroke="#fff" stroke-width="2" fill="none"/></svg></span>
</div>

<!-- Descriptions -->
<h2 class="desc-title abs">BOAT DESRIPTIONS:</h2>
<span class="desc-arrow desc-prev abs"><svg width="12" height="12" viewBox="0 0 12 12"><path d="M8 2 4 6l4 4" stroke="#999" stroke-width="2" fill="none"/></svg></span>
<article class="desc-card" style="left:52px;height:544px">
  <div class="desc-media" role="img" aria-label="Catamaran cockpit with white seating looking out to a palm-lined island" style="background:linear-gradient(180deg,#4f9a5c 0%,#5fb0c8 45%,#e8ecee 70%,#d9dcdc 100%)"></div>
  <h3>Coralia 42</h3>
  <p>Coralia 42 by Harbourline Yards accommodates up to 8 passengers. She has two triple cabins with double and single beds, two private double cabins, and two bathrooms. She also features front nets for lounging and comes equipped with Wi-Fi, Skylinq internet, two kayaks, two paddleboards, snorkeling gear, floaters, and fishing equipment.</p>
</article>
<article class="desc-card" style="left:422px;height:722px">
  <div class="desc-media" role="img" aria-label="Aerial view of a white catamaran with solar panels on turquoise water" style="background:linear-gradient(160deg,#2d9fb6 0%,#47b9c6 50%,#9fd8d4 75%,#e6f0ec 100%)"></div>
  <h3>Tidewell 55 F</h3>
  <p>Tidewell 55F was built by Harbourline Yards and offered as one of our luxury options. She is designed with ample space, making her ideal for private charters with larger groups. Her layout includes four double cabins with private bathrooms; three feature double beds, while one is fitted with two single bunks. Guests can unwind in the generous cockpit and saloon, though the front nets are often the most popular place to lounge. She comes equipped with snorkeling gear, fishing equipment, floating toys, a wakeboard, and paddleboards. Tidewell 55F also provides high-speed Skylinq internet and a fully stocked bar, both included in the charter</p>
</article>
<article class="desc-card" style="left:792px;height:568px">
  <div class="desc-media" role="img" aria-label="White sailing catamaran moored near a green tropical shore under blue sky" style="background:linear-gradient(180deg,#3f86c9 0%,#78b4de 40%,#e9eef0 65%,#3aa8b0 85%,#2b8e97 100%)"></div>
  <h3>Tidewell 37</h3>
  <p>37-foot Tidewell cruising catamaran designed is to accommodate up to six guests in three private double cabins. She offers a comfortable cockpit, a fully equipped kitchen, and a single bathroom. At the bow, a spacious net provides the perfect spot to relax. For activities, she carries snorkeling gear and paddleboards for guests to enjoy.</p>
</article>
<span class="desc-arrow desc-next abs"><svg width="12" height="12" viewBox="0 0 12 12"><path d="m4 2 4 4-4 4" stroke="#fff" stroke-width="2" fill="none"/></svg></span>

<!-- Footer -->
<footer class="site-footer abs">
  <h4 class="foot-head abs" style="left:118px">QUICK LINKS</h4>
  <h4 class="foot-head abs" style="left:461px">CONTACT US</h4>
  <h4 class="foot-head abs" style="left:792px">NEWSLETTER SIGN UP</h4>

  <div class="links abs">
    <a>Fleet</a><a>Itineraries</a>
    <a>About Us</a><a>Activities</a>
    <a>Contact</a><a>Blog</a>
    <a>Pricing</a><a>Languages</a>
    <a>Guna Yala</a><a>BOOK NOW</a>
  </div>

  <div class="contact-list abs">
    <div class="contact-item">
      <span class="contact-icon"><svg width="12" height="12" viewBox="0 0 24 24" fill="#fff"><path d="M6.6 10.8a15 15 0 0 0 6.6 6.6l2.2-2.2c.3-.3.7-.4 1-.2 1.1.4 2.3.6 3.6.6.6 0 1 .4 1 1V20c0 .6-.4 1-1 1A17 17 0 0 1 3 4c0-.6.4-1 1-1h3.5c.6 0 1 .4 1 1 0 1.3.2 2.5.6 3.6.1.3 0 .7-.2 1z"/></svg></span>
      <div>CALL US<br>0123 456 789</div>
    </div>
    <div class="contact-item">
      <span class="contact-icon"><svg width="12" height="10" viewBox="0 0 24 18" fill="none" stroke="#fff" stroke-width="2"><rect x="1" y="1" width="22" height="16"/><path d="m1 1 11 9 11-9"/></svg></span>
      <div>EMAIL US<br>info@bluekeelvoyages.net</div>
    </div>
    <div class="contact-item">
      <span class="contact-icon"><svg width="10" height="13" viewBox="0 0 20 26" fill="#fff"><path d="M10 0a10 10 0 0 0-10 10c0 7 10 16 10 16s10-9 10-16A10 10 0 0 0 10 0zm0 14a4 4 0 1 1 0-8 4 4 0 0 1 0 8z"/></svg></span>
      <div>Address Line goes here,<br>Country Name, 4231</div>
    </div>
  </div>

  <div class="news-input abs">Enter your email</div>
  <div class="news-btn abs">Subscribe</div>

  <div class="foot-rule abs"></div>
  <p class="copyright abs">Copyright © 2025 All Rights Reserved By Company name</p>
  <div class="social abs" aria-label="Social links"><span><i></i></span><span><i></i></span><span><i></i></span><span><i></i></span></div>
</footer>

</body>
</html>
```